Website for BrightlineLabs presentation

We need a new website, ideally as a wordpress there, for BrightlineLabs - we focus on machine learning, big data, data science and data analytics. This website should have two main sections - team presentation, introduction and offered services as static pages, and a blog section.

Target Market(s)

Companies which would like to hire the consultants for data science

Industry/Entity Type

Data Service

Font styles to use
Sans Serif

Colors

Designer to choose colors to be used in the design.

Requirements
Must have
• Wordpress template, blog and presentation pages, nice background images, incorporate the existing logo from brief
Nice to have
• match the word and ppt existing templates for brightline labs

```html
<!DOCTYPE html>
<html lang="en">
<head>
<meta charset="utf-8">
<title>Brightline Labs</title>
<link href="https://fonts.googleapis.com/css2?family=Lato:wght@400;700;900&family=Open+Sans:wght@400;600;700&display=swap" rel="stylesheet">
<style>
:root{
  --blue:#1b73c2;
  --blue-dark:#0d4f93;
  --blue-deep:#0a1a3a;
  --ink:#1f1f1f;
  --text:#666;
  --muted:#9a9a9a;
  --line:#e3e3e3;
  --light:#f4f5f7;
  --footer:#2a2a2a;
  --white:#fff;
}
*{margin:0;padding:0;box-sizing:border-box}
html,body{width:1200px;height:3488px;overflow:hidden;background:var(--white)}
body{position:relative;font-family:"Open Sans",Arial,sans-serif;color:var(--text)}
.abs{position:absolute}
.heading{font-family:"Lato",Arial,sans-serif;font-weight:700;color:var(--ink)}

/* header */
.header{left:0;top:0;width:1200px;height:126px;border-top:4px solid var(--blue);background:var(--white)}
.brand{left:105px;top:28px;display:flex;align-items:center;gap:12px}
.brand-dot{width:22px;height:22px;border-radius:50%;background:var(--blue)}
.brand-name{font-family:"Lato",sans-serif;font-weight:900;font-size:30px;color:var(--blue)}
.topbar{right:105px;top:34px;font-size:14px;color:#777;display:flex;gap:18px;align-items:center}
.topbar svg{vertical-align:-2px;margin-right:6px}
.nav{left:0;top:76px;width:1200px;font-family:"Lato",sans-serif;font-weight:700;font-size:15px;color:#333}
.nav span{position:absolute;top:0}
.nav .active{color:var(--blue)}

/* hero */
.hero{left:0;top:126px;width:1200px;height:560px;background:radial-gradient(ellipse at 50% 45%,#2a7de8 0%,#0f3f99 35%,#071a44 65%,#03081a 100%)}
.hero-title{left:0;top:370px;width:1200px;text-align:center;font-family:"Lato",sans-serif;font-weight:900;font-size:56px;color:var(--white);letter-spacing:1px}

/* side labels */
.side{left:0;width:80px}
.side-label{position:absolute;left:40px;transform:translate(-50%,-50%) rotate(-90deg);font-family:"Lato",sans-serif;font-weight:700;font-size:20px;letter-spacing:4px;white-space:nowrap}
.side-bar{position:absolute;left:38px;width:4px;height:14px;background:var(--blue)}

/* about */
.about{left:0;top:686px;width:1200px;height:470px;background:var(--white)}
.about-img{left:98px;top:100px;width:437px;height:254px;background:linear-gradient(135deg,#5a6f8c,#9fb2c9 50%,#2d4b78);border:6px solid #fff;box-shadow:0 2px 10px rgba(0,0,0,.2)}
.about-ghost{left:1110px;top:55px;width:100px;height:360px}
.about h2{position:absolute;left:595px;top:95px;font-size:30px}
.about p{position:absolute;left:595px;top:160px;width:505px;font-size:13.5px;line-height:24px;color:#777}
.btn{display:inline-flex;align-items:center;justify-content:center;background:var(--blue);color:#fff;font-family:"Lato",sans-serif;font-weight:700;border-radius:22px}
.about .btn{position:absolute;left:595px;top:310px;width:160px;height:44px;font-size:14px}

/* services */
.services{left:0;top:1156px;width:1200px;height:605px;background:linear-gradient(160deg,#1d7fd1,#155fa8 60%,#1470bf)}
.ghost{font-family:"Lato",sans-serif;font-weight:900;white-space:nowrap}
.services .ghost{position:absolute;left:0;top:74px;width:1200px;text-align:center;font-size:64px;color:rgba(255,255,255,.12)}
.services h2{position:absolute;left:0;top:92px;width:1200px;text-align:center;font-family:"Lato",sans-serif;font-weight:900;font-size:30px;color:#fff}
.services .lead{position:absolute;left:0;top:164px;width:1200px;text-align:center;font-size:13px;line-height:24px;color:#e8f1fb}
.card{position:absolute;top:240px;width:233px;height:272px;background:#fff;text-align:center;padding-top:38px}
.card h3{font-family:"Lato",sans-serif;font-weight:700;font-size:19px;color:var(--ink);margin-top:22px}
.card p{font-size:12.5px;line-height:21px;color:#777;margin:12px 28px 0}

/* team */
.team{left:0;top:1761px;width:1200px;height:642px;background:linear-gradient(#f0f1f3,#f6f7f8)}
.team .ghost{position:absolute;left:0;top:70px;width:1200px;text-align:center;font-size:64px;color:rgba(0,0,0,.05)}
.team h2{position:absolute;left:0;top:88px;width:1200px;text-align:center;font-size:30px;font-weight:900}
.team .lead{position:absolute;left:0;top:143px;width:1200px;text-align:center;font-size:13px;color:#777}
.member{position:absolute;width:482px;height:175px}
.member.raised{background:#fff;box-shadow:0 3px 14px rgba(0,0,0,.12)}
.avatar{position:absolute;left:21px;top:22px;width:130px;height:130px;border-radius:50%;border:4px solid #1d2a3a;background:linear-gradient(#cfd6df,#7e8fa5)}
.member h4{position:absolute;left:186px;top:30px;font-family:"Lato",sans-serif;font-weight:700;font-size:19px;color:var(--ink)}
.member .role{position:absolute;left:186px;top:62px;font-size:14px;font-weight:600;color:var(--blue)}
.member p{position:absolute;left:186px;top:94px;width:290px;font-size:12.5px;line-height:21px;color:#888}

/* blog */
.blog{left:0;top:2403px;width:1200px;height:732px;background:var(--white)}
.blog .ghost{position:absolute;left:768px;top:52px;font-size:64px;color:rgba(0,0,0,.07)}
.blog h2{position:absolute;left:133px;top:86px;font-size:30px;font-weight:900}
.blog .lead{position:absolute;left:133px;top:146px;width:940px;font-size:13.5px;line-height:25px;color:#666}
.posts{position:absolute;left:133px;top:230px;width:940px;border-top:1px solid var(--line)}
.post{position:relative;height:78px;border-bottom:1px solid var(--line);display:flex;align-items:center}
.post .date{width:211px;padding-left:30px;font-size:14px;color:#555;display:flex;align-items:center;gap:8px}
.post .sep{width:1px;height:56px;background:var(--line)}
.post .title{padding-left:44px;font-family:"Lato",sans-serif;font-weight:700;font-size:18px;color:var(--ink)}

/* footer */
.footer{left:0;top:3135px;width:1200px;height:353px}
.foot-img{left:0;top:0;width:400px;height:353px;background:linear-gradient(#7fb0e6,#a9cdef 45%,#1e4f8f 46%,#163a6e)}
.foot-mid{left:400px;top:0;width:400px;height:353px;background:var(--footer);text-align:center;color:#fff}
.foot-map{left:800px;top:0;width:400px;height:353px;background:linear-gradient(135deg,#eef0ea,#e2e6dc)}
.foot-mid h5{position:absolute;left:0;width:400px;font-family:"Lato",sans-serif;font-weight:700;font-size:16px;letter-spacing:.5px}
.email-field{position:absolute;left:58px;top:91px;width:284px;height:38px;background:#fff;border:1px solid #999;text-align:left;padding-left:12px;font-size:13px;line-height:36px;color:#555}
.foot-mid .btn{position:absolute;left:135px;top:140px;width:130px;height:36px;font-size:14px}
.foot-mid .info{position:absolute;left:0;width:400px;font-size:14px;color:#eee}
.foot-mid .info svg{vertical-align:-3px;margin-right:10px}
.copy{position:absolute;left:0;top:305px;width:400px;font-size:13px;color:#ddd}
.to-top{left:572px;top:-30px;width:58px;height:58px;border-radius:50%;background:#fff;box-shadow:0 2px 8px rgba(0,0,0,.2);display:flex;align-items:center;justify-content:center}
.direction{position:absolute;left:18px;top:18px;background:#fff;box-shadow:0 1px 4px rgba(0,0,0,.25);font-size:12px;font-weight:600;color:#333;padding:6px 12px}
</style>
</head>
<body>

<header class="abs header">
  <div class="abs brand"><div class="brand-dot"></div><div class="brand-name">BrightlineLabs</div></div>
  <div class="abs topbar">
    <span><svg width="14" height="14" viewBox="0 0 24 24"><path fill="#1b73c2" d="M6.6 10.8a15 15 0 0 0 6.6 6.6l2.2-2.2c.3-.3.7-.4 1-.2 1.1.4 2.3.6 3.6.6.6 0 1 .4 1 1V20c0 .6-.4 1-1 1A17 17 0 0 1 3 4c0-.6.4-1 1-1h3.5c.6 0 1 .4 1 1 0 1.3.2 2.5.6 3.6.1.3 0 .7-.2 1z"/></svg>(+1) 555 010 2030</span>
    <span style="color:#ccc">|</span>
    <span><svg width="15" height="12" viewBox="0 0 24 18"><path fill="#1b73c2" d="M0 0h24v18H0z"/><path d="M1 1l11 9 11-9" fill="none" stroke="#fff" stroke-width="2"/></svg>office@brightlinelabs.com</span>
  </div>
  <nav class="abs nav">
    <span class="active" style="left:507px">HOME</span>
    <span style="left:580px">ABOUT US</span>
    <span style="left:686px">OUR SERVICES</span>
    <span style="left:821px">BLOG</span>
    <span style="left:891px">TEAM</span>
    <span style="left:963px">CONTACT US</span>
    <span style="left:1086px;top:1px"><svg width="16" height="16" viewBox="0 0 24 24"><circle cx="10" cy="10" r="7" fill="none" stroke="#333" stroke-width="3"/><path d="M15 15l7 7" stroke="#333" stroke-width="3"/></svg></span>
  </nav>
</header>

<section class="abs hero" role="img" aria-label="Glowing blue circuit-board brain over a dark background with binary digits">
</section>
<div class="abs hero-title">BRIGHTLINE LABS</div>

<section class="abs about">
  <div class="side abs" style="top:0;height:470px">
    <div class="side-label" style="top:198px;color:#222">ABOUT US</div>
    <div class="side-bar" style="top:310px"></div>
  </div>
  <div class="abs about-img" role="img" aria-label="Hand touching a hexagon diagram of machine learning topics"></div>
  <div class="abs about-ghost"><div class="ghost" style="position:absolute;left:50px;top:180px;transform:translate(-50%,-50%) rotate(90deg);font-size:60px;color:rgba(0,0,0,.07)">ABOUT US</div></div>
  <h2 class="heading">WELCOME TO BRIGHTLINE LABS</h2>
  <p>At vero eos et accusamus et iusto odio dignissimos ducimus qui blanditiis praesentium voluptatum deleniti atque corrupti quos dolores et quas molestias excepturi sint occae cati cupiditate non provident, similique sunt in culpa qui officia deserunt mollitia animi, id est laborum et dolorum fuga. Et harum quidem rerum facilis est et expedita distinctio. Nam libero tempore, cum soluta nobis est eligendi optio cumque</p>
  <span class="btn">READ MORE&nbsp;<svg width="14" height="14" viewBox="0 0 24 24"><circle cx="12" cy="12" r="11" fill="#fff"/><path d="M10 7l5 5-5 5" fill="none" stroke="#1b73c2" stroke-width="3"/></svg></span>
</section>

<section class="abs services">
  <div class="side abs" style="top:0;height:605px">
    <div class="side-label" style="top:250px;color:#fff">SERVICES</div>
    <div class="side-bar" style="top:377px;background:#fff"></div>
  </div>
  <div class="ghost">OUR SERVICES</div>
  <h2>OUR SERVICES</h2>
  <p class="lead">Nam libero tempore, cum soluta nobis est eligendi optio cumque nihil impedit quo minus id quod maxime<br>placeat facere possimus, omnis voluptas assumenda est,</p>

  <div class="card" style="left:100px">
    <svg width="100" height="90" viewBox="0 0 100 90"><g fill="none" stroke="#2a3c52" stroke-width="2"><rect x="28" y="22" width="44" height="44" rx="3"/><path d="M38 22V8M50 22V8M62 22V8M38 66v16M50 66v16M62 66v16M28 34H8M28 54H8M72 34h20M72 54h20"/><circle cx="38" cy="6" r="3"/><circle cx="50" cy="6" r="3"/><circle cx="62" cy="6" r="3"/><circle cx="38" cy="84" r="3"/><circle cx="50" cy="84" r="3"/><circle cx="62" cy="84" r="3"/><circle cx="6" cy="34" r="3"/><circle cx="6" cy="54" r="3"/><circle cx="94" cy="34" r="3"/><circle cx="94" cy="54" r="3"/></g><rect x="34" y="30" width="32" height="28" fill="#1b73c2"/><circle cx="50" cy="44" r="6" fill="#fff"/></svg>
    <h3>Machine Learning</h3>
    <p>Nam libero tempore, cum soluta nobis est eligendi optio</p>
  </div>
  <div class="card" style="left:356px">
    <svg width="100" height="90" viewBox="0 0 100 90"><g fill="none" stroke="#2a3c52" stroke-width="2"><rect x="28" y="22" width="44" height="44" rx="3"/><path d="M38 22V8M50 22V8M62 22V8M38 66v16M50 66v16M62 66v16M28 34H8M28 54H8M72 34h20M72 54h20"/><circle cx="38" cy="6" r="3"/><circle cx="50" cy="6" r="3"/><circle cx="62" cy="6" r="3"/><circle cx="38" cy="84" r="3"/><circle cx="50" cy="84" r="3"/><circle cx="62" cy="84" r="3"/><circle cx="6" cy="34" r="3"/><circle cx="6" cy="54" r="3"/><circle cx="94" cy="34" r="3"/><circle cx="94" cy="54" r="3"/></g><rect x="34" y="30" width="32" height="28" fill="#1b73c2"/><circle cx="50" cy="44" r="6" fill="#fff"/></svg>
    <h3>Big Data</h3>
    <p>Nam libero tempore, cum soluta nobis est eligendi optio</p>
  </div>
  <div class="card" style="left:612px">
    <svg width="100" height="90" viewBox="0 0 100 90"><g fill="none" stroke="#2a3c52" stroke-width="2"><rect x="28" y="22" width="44" height="44" rx="3"/><path d="M38 22V8M50 22V8M62 22V8M38 66v16M50 66v16M62 66v16M28 34H8M28 54H8M72 34h20M72 54h20"/><circle cx="38" cy="6" r="3"/><circle cx="50" cy="6" r="3"/><circle cx="62" cy="6" r="3"/><circle cx="38" cy="84" r="3"/><circle cx="50" cy="84" r="3"/><circle cx="62" cy="84" r="3"/><circle cx="6" cy="34" r="3"/><circle cx="6" cy="54" r="3"/><circle cx="94" cy="34" r="3"/><circle cx="94" cy="54" r="3"/></g><rect x="34" y="30" width="32" height="28" fill="#1b73c2"/><circle cx="50" cy="44" r="6" fill="#fff"/></svg>
    <h3>Data Science</h3>
    <p>Nam libero tempore, cum soluta nobis est eligendi optio</p>
  </div>
  <div class="card" style="left:868px">
    <svg width="100" height="90" viewBox="0 0 100 90"><g fill="none" stroke="#2a3c52" stroke-width="2"><rect x="28" y="22" width="44" height="44" rx="3"/><path d="M38 22V8M50 22V8M62 22V8M38 66v16M50 66v16M62 66v16M28 34H8M28 54H8M72 34h20M72 54h20"/><circle cx="38" cy="6" r="3"/><circle cx="50" cy="6" r="3"/><circle cx="62" cy="6" r="3"/><circle cx="38" cy="84" r="3"/><circle cx="50" cy="84" r="3"/><circle cx="62" cy="84" r="3"/><circle cx="6" cy="34" r="3"/><circle cx="6" cy="54" r="3"/><circle cx="94" cy="34" r="3"/><circle cx="94" cy="54" r="3"/></g><rect x="34" y="30" width="32" height="28" fill="#1b73c2"/><circle cx="50" cy="44" r="6" fill="#fff"/></svg>
    <h3>Data Analytics</h3>
    <p>Nam libero tempore, cum soluta nobis est eligendi optio</p>
  </div>
</section>

<section class="abs team">
  <div class="side abs" style="top:0;height:642px">
    <div class="side-label" style="top:290px;color:#222">OUR TEAM</div>
    <div class="side-bar" style="top:413px"></div>
  </div>
  <div class="ghost">OUR TEAM</div>
  <h2 class="heading">OUR TEAM</h2>
  <p class="lead">We understand the success secrets of the world's most successful business teams.</p>

  <div class="member" style="left:100px;top:176px">
    <div class="avatar" role="img" aria-label="Portrait photo of the founder"></div>
    <h4>MARCUS HALE</h4><div class="role">Founder &amp; CEO</div>
    <p>Nemo enim ipsam voluptatem quia voluptas sit aspernatur aut odit aut fugit sed quia</p>
  </div>
  <div class="member" style="left:616px;top:176px">
    <div class="avatar" role="img" aria-label="Portrait photo of the creative manager"></div>
    <h4>ARJUN MEHTA</h4><div class="role">Creative Manager</div>
    <p>Nemo enim ipsam voluptatem quia voluptas sit aspernatur aut odit aut fugit sed quia</p>
  </div>
  <div class="member raised" style="left:100px;top:367px">
    <div class="avatar" role="img" aria-label="Portrait photo of the general manager"></div>
    <h4>CLARA VOSS</h4><div class="role">General Manager</div>
    <p>Nemo enim ipsam voluptatem quia voluptas sit aspernatur aut odit aut fugit sed quia</p>
  </div>
  <div class="member" style="left:616px;top:367px">
    <div class="avatar" role="img" aria-label="Portrait photo of the administrative lead"></div>
    <h4>OWEN PRYCE</h4><div class="role">Adminstrative Team</div>
    <p>Nemo enim ipsam voluptatem quia voluptas sit aspernatur aut odit aut fugit sed quia</p>
  </div>
</section>

<section class="abs blog">
  <div class="side abs" style="top:0;height:732px">
    <div class="side-label" style="top:320px;color:#222">BLOG POST</div>
    <div class="side-bar" style="top:445px"></div>
  </div>
  <div class="ghost">BLOG POST</div>
  <h2 class="heading">BLOG POST</h2>
  <p class="lead">Nam libero tempore, cum soluta nobis est eligendi optio cumque nihil impedit quo minus id quod maxime placeat facere possimus, omnis voluptas tassumenda est, omnis dolor repellendus. Temporibus autem quibusdam et aut officiis debitis aut rerum necessitatibus saepe eveniet</p>
  <div class="posts">
    <div class="post"><div class="date"><svg width="13" height="13" viewBox="0 0 24 24"><path fill="#555" d="M3 5h18v17H3zM7 2h2v4H7zM15 2h2v4h-2z"/><path fill="#fff" d="M5 10h14v10H5z"/></svg>June 08, 2018</div><div class="sep"></div><div class="title">Nam libero tempore, cum soluta nobis est eligendi optio cumque nihil impedit.</div></div>
    <div class="post"><div class="date"><svg width="13" height="13" viewBox="0 0 24 24"><path fill="#555" d="M3 5h18v17H3zM7 2h2v4H7zM15 2h2v4h-2z"/><path fill="#fff" d="M5 10h14v10H5z"/></svg>June 15, 2018</div><div class="sep"></div><div class="title">When our power of choice is untrammelled and when nothing prevents our being.</div></div>
    <div class="post"><div class="date"><svg width="13" height="13" viewBox="0 0 24 24"><path fill="#555" d="M3 5h18v17H3zM7 2h2v4H7zM15 2h2v4h-2z"/><path fill="#fff" d="M5 10h14v10H5z"/></svg>June 18, 2018</div><div class="sep"></div><div class="title">I must explain to you how all this mistaken idea of denouncing pleasure praising.</div></div>
    <div class="post"><div class="date"><svg width="13" height="13" viewBox="0 0 24 24"><path fill="#555" d="M3 5h18v17H3zM7 2h2v4H7zM15 2h2v4h-2z"/><path fill="#fff" d="M5 10h14v10H5z"/></svg>June 22, 2018</div><div class="sep"></div><div class="title">Quis autem vel eum iure reprehenderit qui in ea voluptate velit esse.</div></div>
    <div class="post"><div class="date"><svg width="13" height="13" viewBox="0 0 24 24"><path fill="#555" d="M3 5h18v17H3zM7 2h2v4H7zM15 2h2v4h-2z"/><path fill="#fff" d="M5 10h14v10H5z"/></svg>June 30, 2018</div><div class="sep"></div><div class="title">Excepteur sint occaecat cupidatat non proident, sunt in culpa qui officia id est.</div></div>
  </div>
</section>

<footer class="abs footer">
  <div class="abs foot-img" role="img" aria-label="Glass office building against a blue sky"></div>
  <div class="abs foot-mid">
    <h5 style="top:60px">NEWSLETTER SUBSCRIPTION</h5>
    <div class="email-field">Email</div>
    <span class="btn">SUBSCRIBE</span>
    <h5 style="top:200px">CONTACT US</h5>
    <div class="info" style="top:234px"><svg width="15" height="15" viewBox="0 0 24 24"><path fill="#fff" d="M6.6 10.8a15 15 0 0 0 6.6 6.6l2.2-2.2c.3-.3.7-.4 1-.2 1.1.4 2.3.6 3.6.6.6 0 1 .4 1 1V20c0 .6-.4 1-1 1A17 17 0 0 1 3 4c0-.6.4-1 1-1h3.5c.6 0 1 .4 1 1 0 1.3.2 2.5.6 3.6.1.3 0 .7-.2 1z"/></svg>(+1) 555 010 2030</div>
    <div class="info" style="top:264px"><svg width="15" height="12" viewBox="0 0 24 18"><path fill="#fff" d="M0 0h24v18H0z"/><path d="M1 1l11 9 11-9" fill="none" stroke="#2a2a2a" stroke-width="2"/></svg>info@brightlinelabs.com</div>
    <div class="copy">© Copyright 2018 BrightlineLabs. All Rights Reserved.</div>
  </div>
  <div class="abs foot-map" role="img" aria-label="Street map showing the office location with a red pin">
    <div class="direction">➦ GET DIRECTION</div>
  </div>
  <div class="abs to-top"><svg width="22" height="22" viewBox="0 0 24 24" fill="none" stroke="#333" stroke-width="2.5"><path d="M6 12l6-6 6 6M6 19l6-6 6 6"/></svg></div>
</footer>

</body>
</html>
```